Animal Eye Clinic needs a Business card

We are a new veterinary ophthalmology practice (Ridgeline Pet Vision Care) and we need a business card designed. We only see animal eyes - we are not a regular veterinary clinic. We already have a logo. We are looking for a professional, good looking business card to hand out to our clients. We are looking for something simple but professional and contemporary. Our logo is likely the only picture/graphic that needs to be on the card.
Updates

Contact Information for Business Card

Delia Vossman, BSc, DVM, MSc, DipACVO
Veterinary Ophthalmologist

Phone: 250.418.3927
Email: ridgelinepetvisioncare@mailbox-example.net
Website: ridgelinepetvisioncare-example.net
Address: 1874 Thornbury Rd
Kelowna, BC, V1X 4M9

Colors

Designer to choose colors to be used in the design.

Requirements
Must have
• Our logo (attached)

```html
<!DOCTYPE html>
<html lang="en">
<head>
<meta charset="utf-8">
<title>Ridgeline Pet Vision Care – Business Card</title>
<link rel="stylesheet" href="https://fonts.googleapis.com/css2?family=Lato:wght@400;700&display=swap">
<style>
  :root {
    --page-bg: #e9e4dc;
    --card-bg: #7b756d;
    --card-edge: #9a948b;
    --teal: #1a8f8a;
    --text-light: #ece6dd;
    --text-soft: #d6cfc4;
    --icon: #3f6f6c;
  }
  html, body {
    margin: 0;
    padding: 0;
    width: 1200px;
    height: 1047px;
    overflow: hidden;
    background: var(--page-bg);
  }
  .canvas {
    position: relative;
    width: 1200px;
    height: 1047px;
    font-family: "Lato", sans-serif;
  }
  .card {
    position: absolute;
    left: 100px;
    top: 238px;
    width: 1000px;
    height: 572px;
    border-radius: 22px;
    background: var(--card-bg);
    border: 2px solid var(--card-edge);
    box-sizing: border-box;
    overflow: hidden;
    color: var(--text-light);
  }
  .person {
    position: absolute;
    left: 46px;
    top: 52px;
  }
  .person-name {
    margin: 0;
    font-size: 43px;
    font-weight: 700;
    color: var(--teal);
    line-height: 1;
  }
  .person-credentials {
    margin: 8px 0 0;
    font-size: 13px;
    color: var(--text-soft);
  }
  .person-title {
    margin: 22px 0 0;
    font-size: 22px;
    color: var(--text-light);
  }
  .practice {
    position: absolute;
    left: 46px;
    top: 272px;
  }
  .practice-name {
    margin: 0 0 6px;
    font-size: 23px;
    color: var(--teal);
  }
  .practice-address {
    margin: 0;
    font-size: 25px;
    line-height: 33px;
    font-style: normal;
    color: var(--text-light);
  }
  .contact-list {
    position: absolute;
    left: 46px;
    top: 405px;
    margin: 0;
    padding: 0;
    list-style: none;
  }
  .contact-item {
    display: flex;
    align-items: center;
    height: 35px;
    font-size: 22px;
    color: var(--text-light);
  }
  .contact-icon {
    width: 20px;
    height: 20px;
    margin-right: 20px;
    flex: none;
  }
  .brand {
    position: absolute;
    right: 48px;
    top: 150px;
    width: 330px;
    display: flex;
    flex-direction: column;
    align-items: center;
  }
  .brand-dot {
    width: 170px;
    height: 170px;
    border-radius: 50%;
    background: var(--teal);
  }
  .brand-name {
    margin: 26px 0 0;
    font-size: 26px;
    font-weight: 700;
    color: var(--teal);
    text-align: center;
    line-height: 1.25;
  }
</style>
</head>
<body>
<div class="canvas">
  <section class="card">
    <div class="person">
      <h1 class="person-name">Delia Vossman</h1>
      <p class="person-credentials">BSc, DVM, MSc, DipACVO</p>
      <p class="person-title">Veterinary Ophthalmologist</p>
    </div>

    <div class="practice">
      <p class="practice-name">Ridgeline Pet Vision Care</p>
      <address class="practice-address">1874 Thornbury Rd<br>Kelowna, BC, V1X 4M9</address>
    </div>

    <ul class="contact-list">
      <li class="contact-item">
        <svg class="contact-icon" viewBox="0 0 20 20" aria-hidden="true">
          <path d="M5 2 L8 2 L9 6 L7 8 Q9 12 12 13 L14 11 L18 12 L18 15 Q17 18 14 18 Q4 16 2 6 Q2 3 5 2 Z" fill="var(--icon)"/>
        </svg>
        250.418.3927
      </li>
      <li class="contact-item">
        <svg class="contact-icon" viewBox="0 0 20 20" aria-hidden="true">
          <rect x="1" y="4" width="18" height="12" rx="2" fill="var(--icon)"/>
          <path d="M2 5 L10 11 L18 5" fill="none" stroke="var(--card-bg)" stroke-width="1.5"/>
        </svg>
        ridgelinepetvisioncare@mailbox-example.net
      </li>
      <li class="contact-item">
        <svg class="contact-icon" viewBox="0 0 20 20" aria-hidden="true">
          <circle cx="10" cy="10" r="8" fill="none" stroke="var(--icon)" stroke-width="2"/>
          <ellipse cx="10" cy="10" rx="3.5" ry="8" fill="none" stroke="var(--icon)" stroke-width="1.5"/>
          <line x1="2" y1="10" x2="18" y2="10" stroke="var(--icon)" stroke-width="1.5"/>
        </svg>
        www.ridgelinepetvisioncare-example.net
      </li>
    </ul>

    <div class="brand">
      <div class="brand-dot"></div>
      <p class="brand-name">Ridgeline Pet Vision Care</p>
    </div>
  </section>
</div>
</body>
</html>
```